Brightfen Business Card Redesign & Logo Update

We need to update our business cards to something more modern and fresh. Brightfen can provide the current color schemes and old design examples, but welcome creativity in helping us with this redesign. PLEASE NOTE that we no longer utilize the "tree" and/or "leaf" imagery in our branding. If able would apprecaite an update on the quality of our "words only" logo in Ai. / PNG formats too.

Target Market(s)

Investors, landowners, corporate partners, contractors

Industry/Entity Type

Environmental Restoration & Conservation

Contact Information for Business Card

Logo, persons name, title, mailing address, phone and email, website url

Font styles to use
Other font styles liked:
• Merriweather

Requirements
Nice to have
• Logo, persons name, title, mailing address, phone and email, website url, but open to ideams
Should not have
• No all back backgrounds

```html
<!DOCTYPE html>
<html lang="en">
<head>
<meta charset="utf-8">
<title>Brightfen Business Card</title>
<link href="https://fonts.googleapis.com/css2?family=Open+Sans:wght@400;700&display=swap" rel="stylesheet">
<style>
  :root {
    --stage: #d7dade;
    --card-dark: #232227;
    --brand-green: #12853f;
    --brand-orange: #ef7d1f;
    --text-light: #ffffff;
  }
  html, body {
    margin: 0;
    padding: 0;
    width: 1200px;
    height: 780px;
    overflow: hidden;
    background: var(--stage);
  }
  .canvas {
    position: relative;
    width: 1200px;
    height: 780px;
    display: flex;
    align-items: center;
    justify-content: center;
    gap: 40px;
  }
  .card {
    position: relative;
    width: 540px;
    height: 309px;
    box-shadow: 0 10px 24px rgba(0,0,0,0.25);
    overflow: hidden;
  }
  .card-frame {
    position: absolute;
    inset: 0;
    width: 100%;
    height: 100%;
  }
  .card-content {
    position: absolute;
    inset: 0;
    font-family: "Open Sans", sans-serif;
  }
  .brand {
    display: flex;
    align-items: center;
  }
  .brand-dot {
    flex: none;
    border-radius: 50%;
    background: var(--brand-green);
  }
  .brand-name {
    font-family: "Open Sans", sans-serif;
    font-weight: 700;
    color: var(--text-light);
    line-height: 1;
    letter-spacing: 0.5px;
  }
  /* Front */
  .front .brand {
    position: absolute;
    inset: 0;
    justify-content: center;
    gap: 16px;
  }
  .front .brand-dot { width: 26px; height: 26px; }
  .front .brand-name { font-size: 60px; }
  /* Back */
  .back .brand {
    position: absolute;
    left: 58px;
    top: 62px;
    gap: 9px;
  }
  .back .brand-dot { width: 14px; height: 14px; }
  .back .brand-name { font-size: 31px; }
  .back .divider {
    position: absolute;
    left: 290px;
    top: 56px;
    width: 1px;
    height: 200px;
    background: linear-gradient(to bottom, rgba(255,255,255,0), var(--text-light) 30%, var(--text-light) 70%, rgba(255,255,255,0));
  }
  .contact-block {
    position: absolute;
    left: 312px;
    top: 96px;
    color: var(--text-light);
  }
  .person-name {
    font-weight: 700;
    font-size: 21px;
    margin: 0;
    line-height: 1.1;
  }
  .person-name .given { color: var(--brand-green); }
  .person-name .family { color: var(--brand-orange); }
  .person-title {
    font-size: 14px;
    margin: 4px 0 14px;
  }
  .contact-list {
    list-style: none;
    margin: 0;
    padding: 0;
    font-size: 12.5px;
  }
  .contact-list li {
    display: flex;
    align-items: center;
    gap: 7px;
    margin-bottom: 5px;
  }
  .contact-icon {
    width: 13px;
    height: 13px;
    flex: none;
  }
</style>
</head>
<body>
<main class="canvas">

  <section class="card front" aria-label="Business card front">
    <svg class="card-frame" viewBox="0 0 540 309" aria-hidden="true">
      <rect width="540" height="309" fill="var(--brand-green)"/>
      <path d="M58,0 H482 Q542,154.5 482,309 H58 Q-2,154.5 58,0 Z" fill="var(--brand-orange)"/>
      <path d="M62,0 H478 Q535,154.5 478,309 H62 Q5,154.5 62,0 Z" fill="var(--card-dark)"/>
    </svg>
    <div class="card-content">
      <div class="brand">
        <span class="brand-dot" aria-hidden="true"></span>
        <span class="brand-name">Brightfen</span>
      </div>
    </div>
  </section>

  <section class="card back" aria-label="Business card back">
    <svg class="card-frame" viewBox="0 0 540 309" aria-hidden="true">
      <rect width="540" height="309" fill="var(--brand-green)"/>
      <path d="M58,0 H482 Q542,154.5 482,309 H58 Q-2,154.5 58,0 Z" fill="var(--brand-orange)"/>
      <path d="M62,0 H478 Q535,154.5 478,309 H62 Q5,154.5 62,0 Z" fill="var(--card-dark)"/>
    </svg>
    <div class="card-content">
      <div class="brand">
        <span class="brand-dot" aria-hidden="true"></span>
        <span class="brand-name">Brightfen</span>
      </div>
      <div class="divider"></div>
      <div class="contact-block">
        <h1 class="person-name"><span class="given">Mirela</span> <span class="family">Vostrova</span></h1>
        <p class="person-title">Managing Director</p>
        <ul class="contact-list">
          <li>
            <svg class="contact-icon" viewBox="0 0 16 16" aria-hidden="true">
              <path d="M3.5 1.5 L6 1.5 L7 5 L5.3 6.2 Q6.6 9.2 9.8 10.7 L11 9 L14.5 10 L14.5 12.5 Q14 14.5 12 14.5 Q2 13.5 1.5 4 Q1.5 2 3.5 1.5 Z" fill="var(--brand-green)"/>
            </svg>
            (555) 214-6093
          </li>
          <li>
            <svg class="contact-icon" viewBox="0 0 16 16" aria-hidden="true">
              <rect x="1" y="3" width="14" height="10" rx="1.5" fill="var(--brand-green)"/>
              <path d="M1.5 4 L8 9 L14.5 4" fill="none" stroke="var(--card-dark)" stroke-width="1.3"/>
            </svg>
            hello@brightfen.com
          </li>
          <li>
            <svg class="contact-icon" viewBox="0 0 16 16" aria-hidden="true">
              <circle cx="8" cy="8" r="7" fill="var(--brand-green)"/>
              <ellipse cx="8" cy="8" rx="3" ry="7" fill="none" stroke="var(--card-dark)" stroke-width="1"/>
              <path d="M1 8 H15 M2.5 4.5 H13.5 M2.5 11.5 H13.5" stroke="var(--card-dark)" stroke-width="1"/>
            </svg>
            www.brightfen.com
          </li>
        </ul>
      </div>
    </div>
  </section>

</main>
</body>
</html>
```